New, modern business card for growing audiology practice

We need a new business card for our audiology practice. Our logo and website have recently changed (more modern) and we want our business cards to reflect this change.
We conduct hearing tests, perform earwax removals, and fit & dispense hearing aids to our patients. We are a family owned practice in which the owner is the one who works directly with the patient. I have attached logos in various formats to use, as well as two ideas I found on this website; as well as a scanned copy of our current logo. Good luck!

Industry/Entity Type

Business

Contact Information for Business Card

Company name: Tolvera Hearing Center
Provider name: Peter Wolstenby, Au.D. F/NSB
Phone number: (440) 683-5127
Address: 837 W. Lindell Ave. Marlow Ridge, OH 44391
email: tolverahearing@postvane.com
website: tolverahearing.com

Colors
000000
aaaaaa
dbdbdb
cacaca
9bcb3c
afd23c
cadf82
b1b1b1

Requirements
Must have
• My card must include information in the "details" section. In the attached images, I found a few that I liked and I would like to model after - "brisky bouncin'" and "Sound Method Center".
• Must be horizontal.
• Must include logos provided. I uploaded them in various file formats and various ways.
• Must match logo font, if possible, if not, please get as close as you can.
Nice to have
• I really like the idea of having a color on one side with just the logo and company name and the contact information and provider name on the other side. I also really like the idea of having the main color dominating on the logo/company side with accent of that same color on the contact side of the card.
Should not have
• Must not be vertical.

```html
<!DOCTYPE html>
<html lang="en">
<head>
<meta charset="utf-8">
<title>Tolvera Hearing Center – Business Card</title>
<link rel="stylesheet" href="https://fonts.googleapis.com/css2?family=Montserrat:wght@300;400;500&display=swap">
<style>
  :root {
    --green: #7aa843;
    --ink: #111111;
    --white: #ffffff;
    --rule: #3a3a3a;
    --stage: #dbdbdb;
  }
  * { box-sizing: border-box; margin: 0; padding: 0; }
  html, body {
    width: 1200px; height: 900px; overflow: hidden;
    background: var(--stage);
    font-family: "Montserrat", Arial, sans-serif;
  }
  .canvas { position: relative; width: 1200px; height: 900px; }
  .card {
    position: absolute; left: 250px; width: 700px; height: 400px;
    overflow: hidden;
    box-shadow: 0 6px 18px rgba(0,0,0,0.18);
  }
  /* Front side */
  .card-front {
    top: 35px; background: var(--green);
    display: flex; align-items: center; justify-content: center;
  }
  .front-brand {
    display: flex; align-items: center; gap: 18px;
    color: var(--white); font-weight: 400; font-size: 30px;
    letter-spacing: 1px; text-transform: uppercase;
  }
  .front-brand .mark-dot {
    width: 26px; height: 26px; border-radius: 50%; background: var(--white);
  }
  /* Back side */
  .card-back { top: 465px; background: var(--white); }
  .back-top {
    position: absolute; left: 0; top: 0; width: 100%; height: 232px;
    background: var(--white);
  }
  .back-brand {
    position: absolute; left: 70px; right: 40px; top: 74px;
    display: flex; align-items: center; gap: 16px;
    font-size: 36px; font-weight: 400; color: var(--ink);
    text-transform: uppercase; letter-spacing: 0.5px; white-space: nowrap;
  }
  .back-brand .mark-dot {
    width: 22px; height: 22px; border-radius: 50%; background: var(--green); flex: none;
  }
  .address {
    position: absolute; left: 0; width: 100%; top: 168px;
    text-align: center; font-size: 15px; font-weight: 400; color: var(--ink);
  }
  .divider {
    position: absolute; left: 0; top: 232px; width: 100%; height: 5px;
    background: var(--rule);
  }
  .back-band {
    position: absolute; left: 0; top: 237px; width: 100%; height: 163px;
    background: var(--green);
  }
  .band-tab { position: absolute; width: 4px; height: 40px; background: var(--white); }
  .band-tab.left { left: 0; bottom: 20px; }
  .band-tab.right { right: 0; top: 0; }
  .contact {
    position: absolute; right: 34px; top: 16px;
    list-style: none; text-align: right;
    font-size: 14.5px; color: var(--ink); line-height: 22px;
  }
  .contact li { display: flex; align-items: center; justify-content: flex-end; gap: 10px; }
  .contact svg { width: 13px; height: 13px; fill: var(--white); flex: none; }
  .provider { position: absolute; left: 32px; bottom: 26px; }
  .provider-name {
    font-size: 22px; font-weight: 300; color: var(--ink);
    text-transform: uppercase; letter-spacing: 0.5px;
  }
  .provider-title { font-size: 14px; color: var(--white); margin-top: 2px; }
</style>
</head>
<body>
<main class="canvas">
  <section class="card card-front" aria-label="Card front">
    <div class="front-brand">
      <span class="mark-dot"></span>
      <span>Tolvera Hearing Center</span>
    </div>
  </section>

  <section class="card card-back" aria-label="Card back">
    <div class="back-top">
      <div class="back-brand">
        <span class="mark-dot"></span>
        <span>Tolvera Hearing Center</span>
      </div>
      <p class="address">837 W. Lindell Ave., Marlow Ridge, OH 44391</p>
    </div>
    <div class="divider"></div>
    <div class="back-band">
      <span class="band-tab right"></span>
      <span class="band-tab left"></span>
      <ul class="contact">
        <li>(440) 683-5127
          <svg viewBox="0 0 24 24" aria-hidden="true"><path d="M6.6 10.8a15.1 15.1 0 0 0 6.6 6.6l2.2-2.2a1 1 0 0 1 1-.25 11.4 11.4 0 0 0 3.6.57 1 1 0 0 1 1 1V20a1 1 0 0 1-1 1A17 17 0 0 1 3 4a1 1 0 0 1 1-1h3.5a1 1 0 0 1 1 1c0 1.25.2 2.45.57 3.57a1 1 0 0 1-.25 1z"/></svg>
        </li>
        <li>tolverahearing@postvane.com
          <svg viewBox="0 0 24 24" aria-hidden="true"><path d="M2 5h20v14H2z M2 5l10 8 10-8" fill="none" stroke="#fff" stroke-width="2"/></svg>
        </li>
        <li>www.tolverahearing.com
          <svg viewBox="0 0 24 24" aria-hidden="true"><circle cx="12" cy="12" r="9" fill="none" stroke="#fff" stroke-width="2"/><path d="M3 12h18M12 3c3 3 3 15 0 18M12 3c-3 3-3 15 0 18" fill="none" stroke="#fff" stroke-width="1.6"/></svg>
        </li>
      </ul>
      <div class="provider">
        <p class="provider-name">Peter Wolstenby</p>
        <p class="provider-title">Au.D. F/NSB</p>
      </div>
    </div>
  </section>
</main>
</body>
</html>
```